Moravel Aesthetic Doctor

I require an elegant, luxurious looking business card for my aesthetic business. I am a doctor and that will set me aside from competitors. I am planning to provide home and spa based treatments to clients with high expectations. I have attached my logo.

```html
<!DOCTYPE html>
<html lang="en">
<head>
<meta charset="utf-8">
<title>Moravel Aesthetic Doctor – Business Card</title>
<link rel="stylesheet" href="https://fonts.googleapis.com/css2?family=Marcellus&family=Roboto:wght@400;500&family=Roboto+Condensed:wght@700&display=swap">
<style>
  :root {
    --backdrop: #c4c4c4;
    --card: #f1f1f1;
    --card-edge: #e4e4e4;
    --brand-grey: #8f959c;
    --brand-blue: #3f9fd8;
    --band-deep: #1566a8;
    --band-light: #4a9fd6;
    --ink: #2b2b2b;
    --ink-soft: #3a3a3a;
  }
  * { box-sizing: border-box; margin: 0; padding: 0; }
  html, body { width: 1200px; height: 576px; overflow: hidden; }
  body {
    background: var(--backdrop);
    position: relative;
    font-family: "Roboto", Arial, sans-serif;
  }
  .card {
    position: absolute;
    width: 484px;
    height: 293px;
    background: linear-gradient(180deg, #f6f6f6 0%, var(--card) 60%, var(--card-edge) 100%);
    border-radius: 12px;
    overflow: hidden;
  }
  .card--front { left: 82px; top: 139px; }
  .card--back { left: 602px; top: 138px; }

  .brand { position: absolute; }
  .brand__mark {
    position: absolute;
    border-radius: 50%;
    border: 2px solid var(--brand-grey);
  }
  .brand__name {
    position: absolute;
    font-family: "Marcellus", Georgia, serif;
    font-weight: 400;
    color: var(--brand-grey);
    text-transform: uppercase;
    white-space: nowrap;
    line-height: 1;
  }

  .card--front .brand__mark { left: 82px; top: 59px; width: 92px; height: 92px; }
  .card--front .brand__name--main { left: 196px; top: 78px; font-size: 41px; letter-spacing: 1px; }
  .card--front .brand__name--sub { left: 200px; top: 124px; font-size: 19px; letter-spacing: 1.5px; }

  .services {
    position: absolute;
    left: 0; right: 0; top: 192px;
    text-align: center;
    font-size: 13.5px;
    line-height: 19px;
    color: var(--ink-soft);
  }
  .services__sep { color: var(--brand-blue); margin: 0 8px; }

  .band {
    position: absolute;
    left: 0; right: 0; top: 239px; height: 34px;
    background: linear-gradient(90deg, var(--band-deep) 0%, var(--band-light) 55%, var(--band-deep) 100%);
    color: #ffffff;
    font-size: 12.5px;
    letter-spacing: 1.2px;
    text-align: center;
    line-height: 34px;
    text-transform: uppercase;
  }

  .card--back .brand__mark { left: 38px; top: 116px; width: 60px; height: 60px; }
  .card--back .brand__name--main { left: 114px; top: 127px; font-size: 25px; letter-spacing: 0.5px; }
  .card--back .brand__name--sub { left: 116px; top: 156px; font-size: 12px; letter-spacing: 1px; }

  .contact { position: absolute; left: 284px; top: 74px; }
  .contact__name {
    font-family: "Roboto Condensed", "Arial Narrow", sans-serif;
    font-weight: 700;
    font-size: 17px;
    color: var(--ink);
  }
  .contact__post { font-family: "Roboto", Arial, sans-serif; font-weight: 400; font-size: 10px; color: var(--brand-blue); margin-left: 3px; }
  .contact__credential { margin-top: 4px; font-size: 12.5px; line-height: 16px; color: var(--brand-blue); }
  .contact__list { list-style: none; margin-top: 12px; }
  .contact__item {
    display: flex; align-items: center; gap: 9px;
    font-size: 12.5px; line-height: 18.5px; color: var(--ink-soft);
  }
  .contact__item svg { width: 11px; height: 11px; fill: var(--brand-blue); flex: none; }
  .contact__follow { display: flex; align-items: center; gap: 6px; margin-top: 4px; font-size: 12.5px; color: var(--ink-soft); }
  .contact__social { width: 12px; height: 12px; border-radius: 50%; background: var(--brand-blue); }
</style>
</head>
<body>

<section class="card card--front" aria-label="Card front">
  <div class="brand">
    <span class="brand__mark" aria-hidden="true"></span>
    <span class="brand__name brand__name--main">Moravel</span>
    <span class="brand__name brand__name--sub">Aesthetic Doctor</span>
  </div>
  <p class="services">
    Dermal Injectables<span class="services__sep">|</span>Plasma Facials<span class="services__sep">|</span>Microneedling<br>
    Skin Boosters<span class="services__sep">|</span>Excessive Sweating
  </p>
  <div class="band">Home and spa based treatments</div>
</section>

<section class="card card--back" aria-label="Card back">
  <div class="brand">
    <span class="brand__mark" aria-hidden="true"></span>
    <span class="brand__name brand__name--main">Moravel</span>
    <span class="brand__name brand__name--sub">Aesthetic Doctor</span>
  </div>
  <div class="contact">
    <p class="contact__name">Dr Elise Varner<span class="contact__post">MRCPCH MD</span></p>
    <p class="contact__credential">Australasian Diploma<br>of Aesthetic Medicine</p>
    <ul class="contact__list">
      <li class="contact__item">
        <svg viewBox="0 0 24 24" aria-hidden="true"><path d="M6.6 10.8a15.1 15.1 0 0 0 6.6 6.6l2.2-2.2a1 1 0 0 1 1-.25 11.4 11.4 0 0 0 3.6.57 1 1 0 0 1 1 1V20a1 1 0 0 1-1 1A17 17 0 0 1 3 4a1 1 0 0 1 1-1h3.5a1 1 0 0 1 1 1c0 1.25.2 2.45.57 3.57a1 1 0 0 1-.25 1z"/></svg>
        0800 555 014
      </li>
      <li class="contact__item">
        <svg viewBox="0 0 24 24" aria-hidden="true"><path d="M2 5h20v14H2z" fill="none"/><path d="M2 5h20v2l-10 6L2 7zM2 9l10 6 10-6v10H2z"/></svg>
        elise@moravel.co.nz
      </li>
      <li class="contact__item">
        <svg viewBox="0 0 24 24" aria-hidden="true"><path d="M12 2a10 10 0 1 0 0 20 10 10 0 0 0 0-20zm6.9 6h-3a15.6 15.6 0 0 0-1.4-3.6A8 8 0 0 1 18.9 8zM12 4c.8 1.2 1.5 2.5 1.9 4h-3.8c.4-1.5 1.1-2.8 1.9-4zM4.3 14a8.2 8.2 0 0 1 0-4h3.4a16 16 0 0 0 0 4zm.8 2h3a15.6 15.6 0 0 0 1.4 3.6A8 8 0 0 1 5.1 16zm3-8h-3a8 8 0 0 1 4.3-3.6A15.6 15.6 0 0 0 8.1 8zM12 20c-.8-1.2-1.5-2.5-1.9-4h3.8c-.4 1.5-1.1 2.8-1.9 4zm2.3-6H9.7a14.7 14.7 0 0 1 0-4h4.6a14.7 14.7 0 0 1 0 4zm.3 5.6a15.6 15.6 0 0 0 1.4-3.6h3a8 8 0 0 1-4.4 3.6zm1.7-5.6a16 16 0 0 0 0-4h3.4a8.2 8.2 0 0 1 0 4z"/></svg>
        www.moravel.co.nz
      </li>
    </ul>
    <p class="contact__follow">Follow us on:
      <span class="contact__social" aria-label="Social profile"></span>
      <span class="contact__social" aria-label="Social profile"></span>
    </p>
  </div>
</section>

</body>
</html>
```